Redesign of business card for Cedar Ridge Mechanical

We are looking for a new design for our business cards for Cedar Ridge Mechanical. We are a plumbing & HVAC construction company, operating on the West Coast of Canada and USA. Logo attached.
Industry/Entity Type
Construction - Plumbing & HVAC
Contact Information for Business Card
Name, address, phone numbers, email, website address
Look and feel
Each slider illustrates characteristics of the customer's brand and the style your logo design should communicate.

```html
<!DOCTYPE html>
<html lang="en">
<head>
<meta charset="utf-8">
<title>Cedar Ridge Mechanical – Business Card</title>
<link href="https://fonts.googleapis.com/css2?family=Montserrat:wght@400;700;800&display=swap" rel="stylesheet">
<style>
  :root {
    --ink: #0b0b0b;
    --paper: #ffffff;
    --stage: #2a2a2a;
    --grey: #8e8e8e;
    --line: #444444;
  }
  * { box-sizing: border-box; margin: 0; padding: 0; }
  html, body { width: 1200px; height: 880px; overflow: hidden; }
  body {
    background: var(--stage);
    font-family: "Montserrat", sans-serif;
    position: relative;
  }
  .card {
    position: absolute;
    left: 250px;
    width: 700px;
    height: 400px;
    border-radius: 28px;
    overflow: hidden;
  }
  .card-front { top: 26px; background: var(--ink); }
  .card-back { top: 454px; background: var(--paper); }

  .wordmark {
    position: absolute;
    display: flex;
    align-items: center;
    gap: 18px;
    font-weight: 800;
    text-transform: uppercase;
    letter-spacing: 1px;
    line-height: 1.05;
  }
  .wordmark-mark { flex: none; }
  .card-front .wordmark {
    left: 0; right: 0; top: 0; bottom: 0;
    justify-content: center;
    color: var(--paper);
    font-size: 40px;
  }
  .card-front .wordmark-mark { width: 46px; height: 46px; background: var(--paper); }
  .card-back .wordmark {
    left: 48px; top: 150px;
    width: 300px;
    color: var(--ink);
    font-size: 27px;
  }
  .card-back .wordmark-mark { width: 36px; height: 36px; background: var(--ink); }

  .divider {
    position: absolute;
    left: 362px; top: 90px;
    width: 1px; height: 200px;
    background: var(--line);
  }
  .contact {
    position: absolute;
    left: 392px; top: 78px;
    color: var(--ink);
  }
  .contact-name { font-size: 25px; font-weight: 800; letter-spacing: 0.5px; }
  .contact-role { font-size: 15px; margin-top: 2px; color: #333; }
  .contact-address { font-size: 15px; margin-top: 14px; line-height: 1.35; color: #222; }
  .contact-list { list-style: none; margin-top: 12px; font-size: 15px; color: #222; }
  .contact-list li { display: flex; align-items: center; gap: 9px; line-height: 1.55; }
  .contact-list svg { width: 14px; height: 14px; fill: var(--ink); flex: none; }

  .swoosh { position: absolute; left: 0; bottom: 0; width: 700px; height: 400px; }
</style>
</head>
<body>

<section class="card card-front">
  <div class="wordmark">
    <span class="wordmark-mark"></span>
    <span>Cedar Ridge<br>Mechanical</span>
  </div>
</section>

<section class="card card-back">
  <svg class="swoosh" viewBox="0 0 700 400" aria-hidden="true">
    <path d="M120 400 C 380 380, 600 330, 700 200 L700 400 Z" fill="var(--grey)"/>
    <path d="M140 400 C 400 388, 610 345, 700 228 L700 400 Z" fill="var(--ink)"/>
  </svg>

  <div class="wordmark">
    <span class="wordmark-mark"></span>
    <span>Cedar Ridge<br>Mechanical</span>
  </div>

  <div class="divider"></div>

  <div class="contact">
    <p class="contact-name">DANIEL REYES</p>
    <p class="contact-role">Managing Director</p>
    <p class="contact-address">Your address, City<br>State, Zip 1234</p>
    <ul class="contact-list">
      <li><svg viewBox="0 0 16 16"><path d="M3 1h3l1.5 4-2 1.2a9 9 0 0 0 4.3 4.3L11 8.5l4 1.5v3a2 2 0 0 1-2 2A13 13 0 0 1 1 3a2 2 0 0 1 2-2z"/></svg>123 456 789</li>
      <li><svg viewBox="0 0 16 16"><path d="M1 3h14v10H1zM2 4.2v.4l6 4 6-4v-.4z"/></svg>info@yourgmail.com</li>
      <li><svg viewBox="0 0 16 16"><circle cx="8" cy="8" r="7"/></svg>www.yourwebsite.com</li>
    </ul>
  </div>
</section>

</body>
</html>
```